Oil and Gas Exploration and Production company needs a business card design

We need a business card design using our logo and colors in the logo. We want a mainstream design.

```html
<!DOCTYPE html>
<html lang="en">
<head>
<meta charset="utf-8">
<title>Vantor Oil &amp; Gas — Business Card</title>
<link rel="stylesheet" href="https://fonts.googleapis.com/css2?family=Arimo:wght@400;700&display=swap">
<style>
  :root {
    --backdrop: #2b2b2b;
    --card: #f4f4f4;
    --ink: #111111;
    --gold: #b8862b;
    --band: #0d0d0d;
    --faint: #c9c9c9;
  }
  * { margin: 0; padding: 0; box-sizing: border-box; }
  html, body {
    width: 1200px; height: 997px; overflow: hidden;
    background: var(--backdrop);
    font-family: "Arimo", Arial, sans-serif;
  }
  .business-card {
    position: absolute; left: 180px; top: 258px;
    width: 840px; height: 480px;
    background: var(--card);
    border-radius: 28px;
    overflow: hidden;
    box-shadow: 0 20px 50px rgba(0,0,0,.55);
  }
  .card-shapes { position: absolute; inset: 0; }
  .brand {
    position: absolute; left: 150px; top: 80px;
    display: flex; align-items: center; gap: 14px;
  }
  .brand-dot { width: 38px; height: 38px; border-radius: 50%; background: var(--gold); }
  .brand-name {
    font-weight: 700; font-size: 44px; color: var(--ink);
    letter-spacing: .5px; line-height: 1;
  }
  .rule {
    position: absolute; left: 70px; top: 196px;
    width: 460px; height: 2px; background: var(--gold);
  }
  .holder { position: absolute; right: 110px; top: 172px; text-align: right; }
  .holder-name { font-weight: 700; font-size: 22px; color: var(--ink); letter-spacing: .5px; }
  .holder-role { font-size: 17px; color: var(--gold); margin-top: 6px; }
  .faint-mark {
    position: absolute; left: 690px; top: 250px;
    width: 96px; height: 96px; border-radius: 50%;
    background: var(--faint); opacity: .6;
  }
  .contacts { position: absolute; left: 56px; top: 318px; list-style: none; }
  .contacts li {
    display: flex; align-items: center; gap: 14px;
    font-size: 18px; color: var(--ink); height: 32px;
  }
  .contacts li.address { color: var(--gold); }
  .contact-icon {
    width: 22px; height: 22px; border-radius: 50%;
    background: var(--gold); flex: none;
    display: flex; align-items: center; justify-content: center;
  }
  .website {
    position: absolute; right: 52px; top: 430px;
    font-weight: 700; font-size: 15px; letter-spacing: 1.8px; color: var(--gold);
    white-space: nowrap;
  }
</style>
</head>
<body>
  <div class="business-card">
    <svg class="card-shapes" width="840" height="480" viewBox="0 0 840 480">
      <path class="gold-strip" d="M0 452 L468 452 C500 452 505 396 548 390 L566 390 C522 398 516 466 478 466 L0 466 Z" fill="var(--gold)"/>
      <path class="dark-band" d="M500 480 C540 480 530 398 590 398 L840 398 L840 480 Z" fill="var(--band)"/>
    </svg>

    <div class="brand">
      <span class="brand-dot"></span>
      <span class="brand-name">VANTOR OIL &amp; GAS</span>
    </div>

    <div class="rule"></div>
    <div class="holder">
      <div class="holder-name">ELIAS MARLOW</div>
      <div class="holder-role">Director of Sales &amp; Marketing</div>
    </div>

    <div class="faint-mark"></div>

    <ul class="contacts">
      <li class="phone">
        <span class="contact-icon">
          <svg width="12" height="12" viewBox="0 0 12 12"><path d="M2 1 L4 1 L5 4 L3.5 5 Q5 7.5 7 8.5 L8 7 L11 8 L11 10 Q11 11 10 11 Q2 10 1 2 Q1 1 2 1 Z" fill="#fff"/></svg>
        </span>612 555 0147
      </li>
      <li class="email">
        <span class="contact-icon">
          <svg width="12" height="12" viewBox="0 0 12 12"><rect x="3" y="1" width="6" height="10" rx="1" fill="none" stroke="#fff" stroke-width="1.3"/><circle cx="6" cy="9" r=".7" fill="#fff"/></svg>
        </span>elias@ridgelineenergy.com
      </li>
      <li class="address">
        <span class="contact-icon">
          <svg width="12" height="12" viewBox="0 0 12 12"><rect x="1" y="3" width="10" height="7" fill="none" stroke="#fff" stroke-width="1.2"/><path d="M1 3 L6 7 L11 3" fill="none" stroke="#fff" stroke-width="1.2"/></svg>
        </span>Millbrook Lane Denton, Leeds
      </li>
    </ul>

    <div class="website">www.vantor-energy.co.uk</div>
  </div>
</body>
</html>
```